Business cards for veterinary clinic

Hi, We are looking for business cards to be designed for our other veterinary clinic. We were very happy with the design done for our other clinic a few months ago. We already have a logo for use which I will attach (please use the image not the text around.
We need a couple of different cards (same design with different names on them) produced

Industry/Entity Type

Veterinary

Contact Information for Business Card

Bellwood Creek Vet Clinic
47 Orchard Rd
Kangaroo Flat
VIC 3555
03) 5182 6390
clinic@bellwoodcreekvetclinic.com.au

Font styles to use
Sans Serif

Colors
0455a3
0592cd

Requirements
Must have
• Three different names
• 1. Generic (no name) with email clinic@bellwoodcreekvetclinic.com.au
• 2. Hollis Varne -Director with email hollis@bellwoodcreekvetclinic.com.au
• 3. Dorian Pike - Vet Director with email hollis@bellwoodcreekvetclinic.com.au

```html
<!DOCTYPE html>
<html lang="en">
<head>
<meta charset="utf-8">
<title>Bellwood Creek Veterinary Clinic – Business Cards</title>
<link rel="stylesheet" href="https://fonts.googleapis.com/css2?family=Lato:wght@300;400;700&display=swap">
<style>
  :root {
    --brand-dark: #0455a3;
    --brand-light: #0592cd;
    --card-back-top: #1176b8;
    --card-back-bottom: #0a5f9c;
    --card-front: #f7f8f9;
    --ink: #3a3d40;
    --rule: #4a4d50;
    --stage: #e4e6e8;
    --white: #ffffff;
  }
  * { box-sizing: border-box; margin: 0; padding: 0; }
  html, body { width: 1200px; height: 997px; overflow: hidden; }
  body {
    background: var(--stage);
    font-family: "Lato", sans-serif;
    position: relative;
  }
  .card {
    position: absolute;
    width: 620px;
    height: 354px;
    border-radius: 26px;
    box-shadow: 0 8px 24px rgba(0,0,0,0.18);
    overflow: hidden;
  }

  /* Back of card */
  .card--back {
    left: 290px;
    top: 110px;
    background: linear-gradient(160deg, var(--card-back-top), var(--card-back-bottom));
    color: var(--white);
  }
  .card--back .back-info {
    position: absolute;
    right: 46px;
    bottom: 44px;
    text-align: right;
  }
  .back-info__name { font-size: 27px; font-weight: 700; letter-spacing: 0.2px; }
  .back-info__tagline { font-size: 15px; font-weight: 300; letter-spacing: 1.2px; margin-top: 6px; opacity: 0.85; }
  .back-info__web { font-size: 16px; font-weight: 700; margin-top: 6px; }

  /* Front of card */
  .card--front {
    left: 290px;
    top: 530px;
    background: var(--card-front);
    color: var(--ink);
  }
  .brand-mark {
    position: absolute;
    left: 40px;
    top: 102px;
    width: 190px;
    display: flex;
    flex-direction: column;
    align-items: center;
    gap: 14px;
  }
  .brand-mark__dot {
    width: 70px; height: 70px; border-radius: 50%;
    background: var(--brand-light);
  }
  .brand-mark__name {
    font-size: 20px; font-weight: 700; color: var(--brand-dark);
    text-align: center; line-height: 1.2;
  }
  .divider {
    position: absolute;
    left: 262px;
    top: 52px;
    width: 3px;
    height: 246px;
    background: var(--rule);
  }
  .contact {
    position: absolute;
    left: 292px;
    top: 58px;
    right: 20px;
  }
  .person { display: flex; align-items: baseline; gap: 14px; }
  .person__name { font-size: 23px; font-weight: 400; letter-spacing: 0.5px; text-transform: uppercase; }
  .person__first { color: var(--brand-light); }
  .person__last { color: var(--brand-dark); }
  .person__role { font-size: 13px; color: var(--ink); }
  .person__email { font-size: 14px; font-weight: 700; margin-top: 4px; }
  .clinic-line { font-size: 21px; margin-top: 26px; }
  .clinic-line__place { color: var(--brand-light); }
  .clinic-line__kind { color: var(--brand-dark); }
  .clinic-web { font-size: 14px; font-weight: 700; margin-top: 12px; }
  .details { list-style: none; margin-top: 8px; }
  .details li {
    display: flex; align-items: center; gap: 12px;
    font-size: 15px; font-weight: 700; margin-top: 6px;
  }
  .details svg { width: 18px; height: 16px; flex: none; fill: var(--brand-dark); }
</style>
</head>
<body>

<section class="card card--back" aria-label="Business card back">
  <div class="back-info">
    <p class="back-info__name">Bellwood Creek Veterinary Clinic</p>
    <p class="back-info__tagline">ALL OF YOUR VETERINARY NEEDS</p>
    <p class="back-info__web">www.bellwoodcreekvetclinic.com.au</p>
  </div>
</section>

<section class="card card--front" aria-label="Business card front">
  <div class="brand-mark">
    <span class="brand-mark__dot"></span>
    <p class="brand-mark__name">Bellwood Creek</p>
  </div>

  <div class="divider"></div>

  <div class="contact">
    <div class="person">
      <p class="person__name"><span class="person__first">Dorian</span> <span class="person__last">Pike</span></p>
      <p class="person__role">Vet Director</p>
    </div>
    <p class="person__email">hollis@bellwoodcreekvetclinic.com.au</p>

    <p class="clinic-line"><span class="clinic-line__place">Bellwood Creek</span> <span class="clinic-line__kind">Veterinary Clinic</span></p>
    <p class="clinic-web">bellwoodcreekvetclinic.com.au</p>

    <ul class="details">
      <li>
        <svg viewBox="0 0 18 16" aria-hidden="true"><path d="M2 5c0-2 3-3 7-3s7 1 7 3v1h-3V4.8c-1-.5-2.5-.8-4-.8s-3 .3-4 .8V6H2z"/><rect x="3" y="7" width="12" height="8" rx="1.5"/></svg>
        (03) 5182 6390
      </li>
      <li>
        <svg viewBox="0 0 18 16" aria-hidden="true"><path d="M1 3h16v10H1z M2.5 4.2 9 9l6.5-4.8V4.2H2.5z" fill-rule="evenodd"/></svg>
        clinic@bellwoodcreekvetclinic.com.au
      </li>
      <li>
        <svg viewBox="0 0 18 16" aria-hidden="true"><path d="M9 1 1 8h2.5v7h4v-4h3v4h4V8H17z"/></svg>
        47 Orchard Rd Ashgrove Vale VIC 3871
      </li>
    </ul>
  </div>
</section>

</body>
</html>
```